Kelo Wave Mint Business cards

Logo, tag line and photo on card
Agent Name
Title
Address
Phone number
Email
Website
Make logo on one side large by rotating  to portrait format.  Keep the background of the logo white.

Contact Information for Business Card
Slogan; Making Every Wave Count

```html
<!DOCTYPE html>
<html lang="en">
<head>
<meta charset="utf-8">
<title>Kelo Wave Mint Business Cards</title>
<link href="https://fonts.googleapis.com/css2?family=Open+Sans:wght@400;600;800&display=swap" rel="stylesheet">
<style>
  :root {
    --stage: #222222;
    --paper: #ffffff;
    --navy: #1f2d66;
    --red: #c42127;
    --ink: #1a1a1a;
    --photo-light: #d9d9d9;
    --photo-dark: #5a5a5a;
  }
  * { box-sizing: border-box; margin: 0; padding: 0; }
  html, body { width: 1200px; height: 711px; overflow: hidden; background: var(--stage); }
  body { position: relative; font-family: "Open Sans", sans-serif; }

  .card {
    position: absolute;
    width: 540px; height: 309px;
    background: var(--paper);
    overflow: hidden;
    box-shadow: 0 10px 24px rgba(0,0,0,.55);
  }
  .card--front { left: 40px; top: 201px; }
  .card--back  { left: 620px; top: 201px; }

  .card__bands { position: absolute; inset: 0; width: 100%; height: 100%; }

  /* Front */
  .brand-mark {
    position: absolute;
    left: 340px; top: 28px;
    width: 170px;
    color: var(--navy);
    font-weight: 800;
    font-size: 46px;
    line-height: 46px;
    letter-spacing: -1px;
  }
  .tagline {
    position: absolute;
    right: 24px; bottom: 30px;
    color: var(--paper);
    font-size: 13px;
    font-weight: 600;
  }

  /* Back */
  .brand-mark--small {
    position: absolute;
    left: 26px; top: 24px;
    color: var(--navy);
    font-weight: 800;
    font-size: 27px;
    line-height: 28px;
    letter-spacing: -.5px;
  }
  .address {
    position: absolute;
    left: 26px; top: 150px;
    color: var(--ink);
    font-size: 13px;
    line-height: 18px;
  }
  .contact-list {
    position: absolute;
    left: 26px; top: 200px;
    list-style: none;
    color: var(--ink);
    font-size: 13px;
    line-height: 21px;
  }
  .contact-list li { display: flex; align-items: center; gap: 8px; }
  .contact-list svg { width: 13px; height: 13px; fill: var(--red); flex: none; }

  .portrait {
    position: absolute;
    left: 340px; top: 30px;
    width: 200px; height: 180px;
    background: radial-gradient(ellipse at 45% 35%, var(--photo-light) 0%, #a8a8a8 45%, var(--photo-dark) 100%);
  }
  .agent {
    position: absolute;
    right: 22px; top: 212px;
    text-align: right;
    color: var(--paper);
    white-space: nowrap;
  }
  .agent__name { font-size: 22px; font-weight: 800; line-height: 28px; }
  .agent__title { font-size: 13px; font-weight: 400; }
</style>
</head>
<body>

<section class="card card--front" aria-label="Business card front">
  <svg class="card__bands" viewBox="0 0 540 309" preserveAspectRatio="none" aria-hidden="true">
    <polygon points="0,300 340,286 334,309 0,309" fill="var(--navy)"/>
    <polygon points="362,236 540,236 540,309 334,309" fill="var(--red)"/>
  </svg>
  <div class="brand-mark">Kelo<br>Wave<br>Mint</div>
  <p class="tagline">Making Every Wave Count</p>
</section>

<section class="card card--back" aria-label="Business card back">
  <div class="portrait" role="img" aria-label="Portrait photo of the managing director"></div>
  <svg class="card__bands" viewBox="0 0 540 309" preserveAspectRatio="none" aria-hidden="true">
    <polygon points="0,296 326,281 318,309 0,309" fill="var(--navy)"/>
    <polygon points="352,196 540,196 540,309 318,309" fill="var(--red)"/>
  </svg>

  <div class="brand-mark--small">Kelo<br>Wave<br>Mint</div>

  <p class="address">4870 Linden Ave. Suite 310<br>Brookvale, TX 75010</p>

  <ul class="contact-list">
    <li>
      <svg viewBox="0 0 24 24" aria-hidden="true"><path d="M6.6 10.8a15.1 15.1 0 0 0 6.6 6.6l2.2-2.2a1 1 0 0 1 1-.25 11.4 11.4 0 0 0 3.6.57 1 1 0 0 1 1 1V20a1 1 0 0 1-1 1A17 17 0 0 1 3 4a1 1 0 0 1 1-1h3.5a1 1 0 0 1 1 1c0 1.250.2 2.45.57 3.57a1 1 0 0 1-.25 1z"/></svg>
      (555) 214-0386
    </li>
    <li>
      <svg viewBox="0 0 24 24" aria-hidden="true"><path d="M3 5h18a1 1 0 0 1 1 1v12a1 1 0 0 1-1 1H3a1 1 0 0 1-1-1V6a1 1 0 0 1 1-1zm1 2.2V17h16V7.2l-8 5.3z"/></svg>
      info@example.com
    </li>
    <li>
      <svg viewBox="0 0 24 24" aria-hidden="true"><path d="M12 2a10 10 0 1 0 0 20 10 10 0 0 0 0-20zm6.9 6h-3a15 15 0 0 0-1.3-3.9A8 8 0 0 1 18.9 8zM12 4c.8 1.2 1.5 2.5 1.9 4h-3.8c.4-1.5 1.1-2.8 1.9-4zM4.3 14a8 8 0 0 1 0-4h3.4a16 16 0 0 0 0 4zm.8 2h3a15 15 0 0 0 1.3 3.9A8 8 0 0 1 5.1 16zm3-8h-3a8 8 0 0 1 4.3-3.9A15 15 0 0 0 8.1 8zM12 20c-.8-1.2-1.5-2.5-1.9-4h3.8c-.4 1.5-1.1 2.8-1.9 4zm2.3-6H9.7a14 14 0 0 1 0-4h4.6a14 14 0 0 1 0 4zm.3 5.9a15 15 0 0 0 1.3-3.9h3a8 8 0 0 1-4.3 3.9zM16.3 14a16 16 0 0 0 0-4h3.4a8 8 0 0 1 0 4z"/></svg>
      www.example.com
    </li>
  </ul>

  <div class="agent">
    <p class="agent__name">Dale Morrow</p>
    <p class="agent__title">Managing Director</p>
  </div>
</section>

</body>
</html>
```